Stonebridge Building and Projects business cards

A business card with watermark background (construction work)

Company logo attached

Home improvement projects
House renovations
Bathroom and kitchen renovations
House extensions
New builds and granny flats

Director Omar Haddani
(Phone number)
omar@sbpbuilding.com.au
(Instagram logo) sbp_building

```html
<!DOCTYPE html>
<html lang="en">
<head>
<meta charset="utf-8">
<title>Stonebridge Building and Projects — Business Cards</title>
<link rel="stylesheet" href="https://fonts.googleapis.com/css2?family=Arimo:wght@400;700&display=swap">
<style>
  :root {
    --brand-blue: #1f6cb3;
    --brand-blue-deep: #1a5d9c;
    --card-white: #ffffff;
    --divider-dark: #2a2d33;
    --stage: #d8d9db;
    --ink-light: #ffffff;
  }
  * { box-sizing: border-box; margin: 0; padding: 0; }
  html, body { width: 1200px; height: 800px; overflow: hidden; }
  body {
    background: var(--stage);
    font-family: "Arimo", Arial, sans-serif;
    display: flex;
    flex-direction: column;
    align-items: center;
    justify-content: center;
    gap: 40px;
  }
  .card {
    width: 600px;
    height: 343px;
    border-radius: 22px;
    overflow: hidden;
    position: relative;
    box-shadow: 0 6px 18px rgba(0,0,0,0.18);
  }

  /* Contact side */
  .card--contact { display: flex; background: var(--brand-blue); }
  .contact__brand {
    width: 44%;
    background: var(--card-white);
    display: flex;
    align-items: center;
    justify-content: center;
    padding: 0 26px;
  }
  .contact__divider {
    width: 6px;
    background: var(--divider-dark);
    border-left: 2px solid var(--card-white);
  }
  .contact__details {
    flex: 1;
    color: var(--ink-light);
    display: flex;
    flex-direction: column;
    align-items: flex-end;
    justify-content: center;
    padding: 0 30px 0 20px;
    text-align: right;
  }
  .contact__name { font-size: 24px; font-weight: 700; letter-spacing: 0.5px; text-transform: uppercase; }
  .contact__role { font-size: 13px; margin-top: 2px; margin-bottom: 26px; }
  .contact__list { list-style: none; }
  .contact__item {
    font-size: 13px;
    line-height: 20px;
    display: flex;
    align-items: center;
    justify-content: flex-end;
    gap: 8px;
  }
  .contact__icon { width: 13px; height: 13px; flex: none; }

  /* Brand lockup */
  .brand-name {
    font-family: "Arimo", Arial, sans-serif;
    font-weight: 700;
    color: var(--brand-blue);
    display: flex;
    align-items: center;
    gap: 10px;
    line-height: 1.15;
  }
  .brand-name__mark { width: 14px; height: 14px; background: currentColor; flex: none; }
  .brand-name--small { font-size: 19px; }
  .brand-name--large { font-size: 30px; color: var(--ink-light); }
  .brand-name--large .brand-name__mark { width: 20px; height: 20px; }

  /* Services side */
  .card--services {
    background: var(--brand-blue);
    color: var(--ink-light);
    display: flex;
    flex-direction: column;
    align-items: center;
    justify-content: space-between;
    padding: 70px 30px 34px;
  }
  .services {
    text-align: center;
    font-size: 14px;
    line-height: 21px;
  }
  .services__sep {
    display: inline-block;
    width: 5px; height: 5px;
    background: var(--ink-light);
    margin: 0 7px 2px;
    vertical-align: middle;
  }
</style>
</head>
<body>

  <section class="card card--contact" aria-label="Business card, contact side">
    <div class="contact__brand">
      <div class="brand-name brand-name--small">
        <span class="brand-name__mark"></span>
        <span>Stonebridge<br>Building and Projects</span>
      </div>
    </div>
    <div class="contact__divider"></div>
    <div class="contact__details">
      <h1 class="contact__name">Omar Haddani</h1>
      <p class="contact__role">Director</p>
      <ul class="contact__list">
        <li class="contact__item">369-482-7130
          <svg class="contact__icon" viewBox="0 0 24 24" fill="#fff" aria-hidden="true"><path d="M6.6 10.8a15 15 0 0 0 6.6 6.6l2.2-2.2c.3-.3.7-.4 1-.2 1.1.4 2.3.6 3.6.6.6 0 1 .4 1 1V20c0 .6-.4 1-1 1A17 17 0 0 1 3 4c0-.6.4-1 1-1h3.5c.6 0 1 .4 1 1 0 1.3.2 2.5.6 3.6.1.3 0 .7-.2 1z"/></svg>
        </li>
        <li class="contact__item">omar@sbpbuilding.com.au
          <svg class="contact__icon" viewBox="0 0 24 24" fill="#fff" aria-hidden="true"><path d="M3 5h18v14H3z"/><path d="M3 5l9 8 9-8" fill="none" stroke="#1f6cb3" stroke-width="2"/></svg>
        </li>
        <li class="contact__item">sbpbuilding.com.au
          <svg class="contact__icon" viewBox="0 0 24 24" aria-hidden="true"><circle cx="12" cy="12" r="10" fill="#fff"/><path d="M2 12h20M12 2c3 3 3 17 0 20M12 2c-3 3-3 17 0 20" fill="none" stroke="#1f6cb3" stroke-width="1.6"/></svg>
        </li>
        <li class="contact__item">sbp_building
          <svg class="contact__icon" viewBox="0 0 24 24" aria-hidden="true"><circle cx="12" cy="12" r="9" fill="none" stroke="#fff" stroke-width="2.4"/></svg>
        </li>
      </ul>
    </div>
  </section>

  <section class="card card--services" aria-label="Business card, services side">
    <div class="brand-name brand-name--large">
      <span class="brand-name__mark"></span>
      <span>Stonebridge<br>Building and Projects</span>
    </div>
    <p class="services">
      Home improvement projects<span class="services__sep"></span>House renovations<span class="services__sep"></span>House extensions<br>
      Bathroom &amp; kitchen renovations<span class="services__sep"></span>New builds &amp; granny flats
    </p>
  </section>

</body>
</html>
```